wine label for ultra premium vineyard in Bendigo, Central Otago, New Zealand

"WREN" is our new wine brand, with grapes grown in our spectacular "ter Hoeven" vineyard. The small, elevated vineyard overlooks a river valley and snowy mountains. We would like a highly elegant label for our 2018 pinot noir wine, which highlights the quality of wine and our very special vineyard location. "WREN" has to be prominent, with secondary emphasis on "ter Hoeven vineyard" and "Bendigo, Central Otago". A stylized WREN logo (bird) could be a useful design device instead of the commonly seen illustrated mountain landscape (which is quite common for our local wines). Label size 90 high, 110 wide. Please use a pinot noir / burgundy bottle. See here for vineyard pics, and also below pics for other local wine labels and pics for inspiration / styles. https://www.instagram.com/jan.ter.hoeven/

Target Market(s)

average bottle price for this premium red pinot noir would be aroundUS$40. target market are generally urban professionals aged 25 and older with a high degree of interest in pinot noir wine, and who are familiar with New Zealand pinot noir (ie. already know several brands).

Colors
ed252d

Requirements
Must have
• distinctive label, sophisticated look
Nice to have
• classy white paper stock
Should not have
• label must not get too busy... less but high quality and distinctive is more....

```html
<!DOCTYPE html>
<html lang="en">
<head>
<meta charset="utf-8">
<title>WREN – Pinot Noir label concepts</title>
<link rel="stylesheet" href="https://fonts.googleapis.com/css2?family=Caveat:wght@500&family=Italianno&family=Playfair+Display:wght@400&family=Quicksand:wght@300;400&display=swap">
<style>
  :root {
    --backdrop: #000000;
    --paper: #e8e7e3;
    --ink-grey: #55564f;
    --frame-grey: #66665f;
    --wine-red: #ed252d;
    --soft-red: #e9505a;
    --brick-red: #b2454a;
    --script-black: #2a2a2a;
    --frame-cyan: #22aad6;
    --frame-navy: #3b3f7a;
    --feather-cyan: #7ff0ea;
    --feather-pink: #e386a8;
  }
  * { box-sizing: border-box; margin: 0; padding: 0; }
  html, body { width: 720px; height: 1200px; overflow: hidden; background: var(--backdrop); }
  .board { position: relative; width: 720px; height: 1200px; }

  .label {
    position: absolute; left: 30px; width: 450px; height: 368px;
    background: var(--paper); overflow: hidden;
  }
  .label--classic { top: 27px; }
  .label--framed  { top: 416px; }
  .label--boxed   { top: 805px; }

  .abs { position: absolute; }
  .centered { left: 0; width: 100%; text-align: center; }

  .details {
    font-family: "Quicksand", sans-serif; font-weight: 300;
    color: var(--soft-red); font-size: 12.5px; letter-spacing: 0.2px; line-height: 1;
  }
  .script {
    font-family: "Italianno", cursive; text-transform: uppercase;
    letter-spacing: 2px; line-height: 1;
  }
  .art { position: absolute; }

  /* Classic label */
  .classic__name {
    top: 26px; font-family: "Caveat", cursive; font-weight: 500;
    font-size: 62px; color: var(--ink-grey); letter-spacing: 2px; line-height: 1;
  }
  .classic__bird {
    left: 193px; top: 134px; width: 64px; height: 48px; border-radius: 45% 55% 40% 50%;
    background: radial-gradient(circle at 40% 40%, #f0402b, #c53022 60%, #3b2a2e);
  }
  .classic__rule { left: 0; width: 100%; height: 1px; background: #222; }
  .classic__vineyard { top: 241px; height: 27px; line-height: 30px; font-size: 26px; color: var(--wine-red); }

  /* Framed label */
  .framed__lines { position: absolute; inset: 0; }
  .framed__bird {
    left: 80px; top: 40px; width: 296px; height: 300px;
    border-radius: 60% 40% 30% 70%;
    background: radial-gradient(ellipse at 55% 40%, rgba(255,255,255,0.8), rgba(255,255,255,0) 70%);
  }
  .framed__feather {
    left: 352px; top: 170px; width: 40px; height: 136px;
    border-radius: 50% 50% 50% 50% / 70% 70% 30% 30%;
    transform: rotate(28deg); transform-origin: 50% 50%;
    background: linear-gradient(to bottom, var(--feather-cyan), var(--feather-pink));
  }
  .framed__name {
    left: 139px; width: 213px; top: 58px; text-align: center;
    font-family: "Playfair Display", serif; font-weight: 400;
    font-size: 74px; color: var(--wine-red); line-height: 1;
  }
  .framed__vineyard {
    left: 139px; width: 240px; top: 192px; text-align: center;
    font-size: 26px; color: var(--wine-red); line-height: 0.55;
  }
  .vertical { transform-origin: 0 0; transform: rotate(-90deg); white-space: nowrap; }
  .framed__year  { left: 93px; top: 113px; font-size: 17px; }
  .framed__variety { left: 93px; top: 276px; font-size: 17px; }
  .framed__region { left: 96px; top: 314px; font-size: 17.5px; font-weight: 300; }

  /* Boxed label */
  .boxed__lines { position: absolute; inset: 0; }
  .boxed__name {
    left: 107px; width: 235px; top: 32px; text-align: center;
    font-family: "Caveat", cursive; font-weight: 500;
    font-size: 48px; color: var(--brick-red); line-height: 1; letter-spacing: 1px;
  }
  .boxed__bird {
    left: 176px; top: 153px; width: 84px; height: 48px; border-radius: 50% 60% 40% 50%;
    background: linear-gradient(135deg, #9aa1a8 0%, #d35868 55%, #2b2b2b 100%);
  }
  .boxed__vineyard {
    left: 406px; top: 349px; font-size: 24px; color: var(--script-black); letter-spacing: 5px;
  }
</style>
</head>
<body>
<main class="board">

  <section class="label label--classic">
    <h1 class="abs centered classic__name">WREN</h1>
    <div class="art classic__bird" role="img" aria-label="Small watercolour illustration of a red wren perched"></div>
    <div class="abs classic__rule" style="top:241px"></div>
    <p class="abs centered script classic__vineyard">ter Hoeven Vineyard</p>
    <div class="abs classic__rule" style="top:268px"></div>
    <p class="abs centered details" style="top:283px">-2018-</p>
    <p class="abs centered details" style="top:312px">PINOT NOIR</p>
    <p class="abs centered details" style="top:341px">BENDIGO, CENTRAL OTAGO, NZ</p>
  </section>

  <section class="label label--framed">
    <div class="art framed__bird" role="img" aria-label="Faint white engraved illustration of a wren on a branch"></div>
    <svg class="framed__lines" width="450" height="368" viewBox="0 0 450 368" aria-hidden="true">
      <defs>
        <linearGradient id="frame-fade" x1="0" y1="0" x2="0" y2="1">
          <stop offset="0" stop-color="var(--frame-cyan)"/>
          <stop offset="0.6" stop-color="#2a8fb8"/>
          <stop offset="1" stop-color="var(--frame-navy)"/>
        </linearGradient>
      </defs>
      <g fill="none" stroke="url(#frame-fade)" stroke-width="1.5">
        <rect x="6.5" y="6.5" width="437" height="356" stroke="url(#frame-fade)"/>
        <rect x="74.5" y="52.5" width="302" height="294"/>
        <rect x="124.5" y="39.5" width="235" height="199"/>
        <rect x="139.5" y="25.5" width="213" height="133"/>
      </g>
    </svg>
    <div class="art framed__feather" role="img" aria-label="Feather in a cyan to pink gradient"></div>
    <h1 class="abs framed__name">WREN</h1>
    <p class="abs script framed__vineyard">ter Hoeven<br>Vineyard</p>
    <p class="abs details vertical framed__year">-2018-</p>
    <p class="abs details vertical framed__variety">PINOT NOIR</p>
    <p class="abs details framed__region">BENDIGO, CENTRAL OTAGO, NZ</p>
  </section>

  <section class="label label--boxed">
    <svg class="boxed__lines" width="450" height="368" viewBox="0 0 450 368" aria-hidden="true">
      <g fill="none" stroke="var(--frame-grey)" stroke-width="1.5">
        <rect x="107.5" y="27.5" width="235" height="198"/>
        <rect x="74.5" y="93.5" width="302" height="265"/>
      </g>
    </svg>
    <h1 class="abs boxed__name">WREN</h1>
    <div class="art boxed__bird" role="img" aria-label="Flat illustration of a grey and rose wren perched"></div>
    <p class="abs centered details" style="top:284px">-2018-</p>
    <p class="abs centered details" style="top:313px">PINOT NOIR</p>
    <p class="abs centered details" style="top:342px">BENDIGO, CENTRAL OTAGO, NZ</p>
    <p class="abs script vertical boxed__vineyard">ter Hoeven Vineyard</p>
  </section>

</main>
</body>
</html>
```